Modern HomePage Design for Church

We are looking for a modern homepage design using the sections we put together in the template. The colors we want are blue, black, grey, and white. We do not want use the colors in the logo. Please modify the logo color to match the website color scheme.

Target Market(s)

Church

Industry/Entity Type

Church

Number of Pages Required

1 page

Colors
0293ce
ffffff
474747
9d9d9d

```html
<!DOCTYPE html>
<html lang="en">
<head>
<meta charset="utf-8">
<title>Riverstone Community Church — Home</title>
<link rel="stylesheet" href="https://fonts.googleapis.com/css2?family=Questrial&family=Josefin+Sans:wght@400;600&family=Kaushan+Script&family=Crimson+Text:ital@0;1&display=swap">
<style>
  :root {
    --blue: #0293ce;
    --white: #ffffff;
    --charcoal: #474747;
    --grey: #9d9d9d;
    --mid-grey: #7f7f7f;
    --nav: #3a3a3a;
    --ink: #1a1a1a;
  }
  * { box-sizing: border-box; margin: 0; padding: 0; }
  html, body { width: 1200px; height: 1200px; overflow: hidden; background: var(--white); }
  body { position: relative; font-family: "Questrial", sans-serif; color: var(--white); }
  .abs { position: absolute; }

  /* Navigation */
  .site-nav { left: 0; top: 70px; width: 1200px; height: 41px; background: var(--nav); }
  .nav-link { position: absolute; top: 16px; font-size: 7.5px; letter-spacing: .3px; color: #cfcfcf; text-transform: uppercase; }
  .nav-link.is-active { color: var(--blue); }
  .give-btn { position: absolute; left: 857px; top: 5px; width: 69px; height: 31px; background: var(--blue);
    font-size: 6.5px; text-transform: uppercase; display: flex; align-items: center; justify-content: center; border-radius: 2px; }

  /* Hero */
  .hero { left: 0; top: 111px; width: 1200px; height: 442px; overflow: hidden;
    background:
      radial-gradient(ellipse 260px 200px at 820px 160px, rgba(255,190,70,.85), rgba(230,110,30,.35) 45%, transparent 75%),
      radial-gradient(ellipse 700px 260px at 600px 470px, rgba(220,100,30,.9), rgba(90,40,60,.5) 55%, transparent 85%),
      linear-gradient(180deg, #050608 0%, #0b0d16 45%, #2a2040 75%, #7a3a20 100%); }
  .brand { left: 278px; top: 136px; width: 90px; text-align: center; }
  .brand-mark { display: block; margin: 0 auto 4px; width: 12px; height: 12px; background: var(--white); border-radius: 50%; }
  .brand-name { font-size: 15px; color: var(--blue); letter-spacing: .5px; }
  .brand-sub { font-size: 5px; color: var(--white); letter-spacing: .4px; text-transform: uppercase; }
  .service-pill { top: 128px; width: 103px; height: 21px; border-radius: 4px; background: rgba(70,70,70,.85);
    font-size: 7px; text-transform: uppercase; display: flex; align-items: center; justify-content: center; }
  .hero-title { left: 29px; top: 208px; font-family: "Josefin Sans", sans-serif; font-size: 46px; font-variant: small-caps;
    letter-spacing: 1.5px; white-space: nowrap; line-height: 1; }
  .hero-script { left: 214px; top: 262px; font-family: "Kaushan Script", cursive; font-size: 84px; line-height: 1.2; }
  .learn-btn { left: 278px; top: 411px; width: 171px; height: 53px; background: rgba(157,157,157,.75);
    font-size: 18px; letter-spacing: .5px; display: flex; align-items: center; justify-content: center; }

  /* Notice band */
  .notice-band { left: 0; top: 553px; width: 1200px; height: 45px; background: var(--blue); }
  .notice-text { position: absolute; left: 170px; top: 17px; font-size: 9.8px; text-transform: uppercase; letter-spacing: .2px; }
  .visitor-btn { position: absolute; left: 818px; top: 11px; width: 103px; height: 23px; background: var(--charcoal);
    font-size: 10px; text-transform: uppercase; display: flex; align-items: center; justify-content: center; }

  /* Welcome */
  .welcome { left: 0; top: 598px; width: 848px; height: 344px; background: var(--mid-grey); }
  .welcome h1 { position: absolute; left: 42px; top: 45px; font-weight: 400; font-size: 13.5px; letter-spacing: .6px; text-transform: uppercase; }
  .welcome-sub { position: absolute; left: 42px; top: 65px; font-size: 9px; color: #c4c4c4; letter-spacing: .3px; }
  .welcome-copy { position: absolute; left: 42px; width: 690px; font-size: 8.6px; color: #c8c8c8; letter-spacing: .25px; }
  .welcome-divider { left: 848px; top: 598px; width: 4px; height: 344px; background: var(--charcoal); }
  .pastor-photo { left: 852px; top: 598px; width: 348px; height: 344px;
    background: linear-gradient(160deg, #f4f4f4 0%, #e6e0dc 40%, #3a2a44 70%, #1d1a24 100%); }

  /* Event */
  .event { left: 0; top: 942px; width: 1200px; height: 188px; background: var(--charcoal); }
  .event h2 { position: absolute; left: 40px; top: 48px; font-family: "Josefin Sans", sans-serif; font-weight: 600;
    font-size: 23px; font-variant: small-caps; letter-spacing: 1px; }
  .event-date { position: absolute; left: 40px; top: 80px; font-size: 15px; letter-spacing: .4px; }
  .event-note { position: absolute; left: 40px; top: 106px; font-family: "Crimson Text", serif; font-size: 10.5px; line-height: 12px; }
  .count-row { position: absolute; left: 504px; height: 30px; width: 160px; }
  .count-label { position: absolute; left: 0; top: 11px; font-size: 9px; font-variant: small-caps; letter-spacing: .4px; }
  .count-down, .count-up { position: absolute; top: 12px; font-size: 7px; }
  .count-down { left: 59px; }
  .count-up { left: 143px; }
  .count-value { position: absolute; left: 86px; top: 0; width: 48px; text-align: center; font-size: 27px; letter-spacing: 2px; }
  .count-rule { position: absolute; left: 576px; width: 62px; height: 1px; background: #bdbdbd; }
  .event-summary { position: absolute; left: 876px; top: 35px; width: 300px; text-align: center; font-family: "Josefin Sans", sans-serif;
    font-size: 12px; line-height: 12px; font-variant: small-caps; letter-spacing: .5px; }
  .read-btn { position: absolute; left: 975px; top: 133px; width: 103px; height: 23px; background: var(--white); color: var(--charcoal);
    font-family: "Crimson Text", serif; font-size: 11px; font-variant: small-caps; letter-spacing: .6px;
    display: flex; align-items: center; justify-content: center; }
</style>
</head>
<body>

<nav class="site-nav abs">
  <span class="nav-link is-active" style="left:280px">Home</span>
  <span class="nav-link" style="left:334px">Team</span>
  <span class="nav-link" style="left:384px">Features</span>
  <span class="nav-link" style="left:454px">Events</span>
  <span class="nav-link" style="left:512px">Sermons</span>
  <span class="nav-link" style="left:582px">Contacts</span>
  <span class="nav-link" style="left:654px">Blog</span>
  <span class="give-btn">Give Online</span>
</nav>

<section class="hero abs" role="img" aria-label="Silhouette of a person kneeling before a large cross against a glowing sunset sky"></section>

<div class="brand abs">
  <span class="brand-mark"></span>
  <div class="brand-name">RIVERSTONE</div>
</div>
<div class="service-pill abs" style="left:709px">Sunday Worship 10:15</div>
<div class="service-pill abs" style="left:822px">Sunday School 09h00</div>
<div class="hero-title abs">Reaching And Resotring Through</div>
<div class="hero-script abs">Revelation!</div>
<div class="learn-btn abs">LEARN MORE &gt;&gt;</div>

<section class="notice-band abs">
  <p class="notice-text">Lorem ipsum dolor sit amet, consectetuer adipiscing elit, sed diam nonummy nibh euismod tincidunt ut</p>
  <span class="visitor-btn">Visitor Info</span>
</section>

<section class="welcome abs">
  <h1>Welcome to Riverstone Community Church</h1>
  <p class="welcome-sub">Lorem ipsum dolor sit amet, consectetuer adipiscing elit, sed</p>
  <p class="welcome-copy" style="top:107px;line-height:26px">Lorem ipsum dolor sit amet, consectetuer adipiscing elit, sed diam nonummy nibh euismod tincidunt ut laoreet dolore magna aliquam erat volutpat. Ut wisi enim ad minim veniam, quis nostrud exerci tation ullamcorper suscipit lobortis nisl ut aliquip ex ea commodo consequat. Duis autem</p>
  <p class="welcome-copy" style="top:193px;line-height:18.5px">Lorem ipsum dolor sit amet, consectetuer adipiscing elit, sed diam nonummy nibh euismod tincidunt ut laoreet dolore magna aliquam erat volutpat. Ut wisi enim ad minim veniam, quis nostrud exerci tation ullamcorper suscipit lobortis nisl ut aliquip ex ea commodo consequat. Duis autem vel eum iriure dolor in hendrerit in vulputate velit esse molestie consequat, vel illum dolore eu feugiat nulla facilisis at vero eros et ac-</p>
</section>
<div class="welcome-divider abs"></div>
<div class="pastor-photo abs" role="img" aria-label="Portrait of the senior pastor and his wife smiling"></div>

<section class="event abs">
  <h2>Church leaders meeting</h2>
  <p class="event-date">Month 00 , 2019 00:00pm</p>
  <p class="event-note"><em>Lorem ipsum dolor sit amet, consectetuer adipiscing elit,<br>sed diam nonummy nibh euismod tincidunt ut</em></p>

  <div class="count-row" style="top:21px"><span class="count-label">Days</span><span class="count-down">▼</span><span class="count-value">00</span><span class="count-up">▲</span></div>
  <div class="count-row" style="top:60px"><span class="count-label">Hours</span><span class="count-down">▼</span><span class="count-value">00</span><span class="count-up">▲</span></div>
  <div class="count-row" style="top:99px"><span class="count-label">Minutes</span><span class="count-down">▼</span><span class="count-value">00</span><span class="count-up">▲</span></div>
  <div class="count-row" style="top:138px"><span class="count-label">Seconds</span><span class="count-down">▼</span><span class="count-value">00</span><span class="count-up">▲</span></div>
  <span class="count-rule" style="top:17px"></span>
  <span class="count-rule" style="top:56px"></span>
  <span class="count-rule" style="top:94px"></span>
  <span class="count-rule" style="top:132px"></span>
  <span class="count-rule" style="top:170px"></span>

  <p class="event-summary">Lorem ipsum dolor sit amet, consectetuer adipiscing elit, sed diam nonummy nibh euismod tincidunt ut laoreet dolore magna aliquam erat volutpat. Ut wisi enim ad minim veniam, quis nostrud exerci tation ullamcorper suscipit lobortis nisl ut aliquip ex ea commodo consequat. Duis autem vel eum iriure</p>
  <span class="read-btn">Read more</span>
</section>

</body>
</html>
```